Multi-Line Insurance PPC Landing Page - Conversion optimized.

We have a PPC landing page used for the general population to get an insurance quote through an agent's site.

We'd like to improve the page for PPC traffic, make it more conversion friendly.

Site should be a single long page.

We will dynamically change the form and headlines on the page depending on what insurance "line" is being called. ie, Lift, Auto, Home, Business.

The enclosed AI file has all of the raw elements we need. We're looking to enhance the design and conversion ability.

Target Market(s)

General public needed insurance services.

Industry/Entity Type

Insurance Broker

Number of Pages Required

1 page

Font styles to use
Sans Serif

Requirements
Must have
• Form, agent picture, name, address.

```html
<!DOCTYPE html>
<html lang="en">
<head>
<meta charset="utf-8">
<title>Insurance Agent – Instant Quote</title>
<link rel="stylesheet" href="https://fonts.googleapis.com/css2?family=Cinzel:wght@400;700&family=Open+Sans:wght@400;600;700&display=swap">
<style>
:root{
  --blue:#1f5fa8;
  --blue-dark:#173f73;
  --navy:#1c2f57;
  --red:#c3272b;
  --ink:#333;
  --muted:#666;
  --grey-band:#ececec;
  --hex:#3c3c3c;
  --line:#cfd6e0;
  --white:#fff;
}
*{box-sizing:border-box;margin:0;padding:0}
html,body{width:721px;height:1200px;overflow:hidden;background:var(--white)}
body{position:relative;font-family:"Open Sans",Arial,sans-serif;color:var(--ink)}

/* header */
.site-header{position:absolute;top:0;left:0;width:721px;height:48px;display:flex;align-items:center;padding:0 20px;justify-content:space-between}
.brand{font-family:"Cinzel",Georgia,serif;font-weight:700;font-size:24px;color:var(--navy);letter-spacing:1px}
.header-actions{display:flex;align-items:center;gap:10px}
.btn{display:inline-block;background:var(--blue);color:var(--white);font-weight:700;font-size:9px;padding:5px 10px;border-radius:2px;letter-spacing:.3px;white-space:nowrap}
.phone{display:flex;align-items:center;gap:5px;color:var(--blue);font-weight:700;font-size:15px}

/* hero */
.hero{position:absolute;top:48px;left:0;width:721px;height:300px;
  background:radial-gradient(ellipse at 50% 30%,#c9c7c1 0%,#8e8d89 40%,#4d4e50 80%,#2f3134 100%)}

/* quote panel */
.quote-panel{position:absolute;top:338px;left:74px;width:574px;height:156px;background:var(--white);
  box-shadow:0 2px 8px rgba(0,0,0,.25);display:flex;border-top:3px solid var(--blue);overflow:hidden}
.agent-card{width:178px;background:#f3f4f6;padding:7px 12px;font-size:7px;color:var(--muted);line-height:1.3}
.agent-photo{width:52px;height:58px;margin:0 auto 4px;display:block}
.agent-title{color:var(--blue);font-weight:700;font-size:9.5px;margin-bottom:3px;white-space:nowrap}
.agent-line{display:flex;align-items:center;gap:4px;margin-bottom:2px;white-space:nowrap}
.agent-address{margin-top:3px;line-height:1.3}
.quote-form{flex:1;padding:8px 16px}
.form-title{font-family:"Cinzel",Georgia,serif;font-weight:700;color:var(--blue);font-size:14px;text-align:center;margin-bottom:6px;white-space:nowrap}
.form-grid{display:grid;grid-template-columns:1fr 1fr;gap:3px 14px}
.field label{display:block;font-size:6.5px;color:var(--muted);margin-bottom:1px}
.input{height:12px;border:1px solid var(--line);background:var(--white);font-size:6px;color:#999;padding:1px 3px;line-height:9px}
.dob{display:flex;gap:3px}
.dob .input{flex:1}
.submit{display:block;margin:6px auto 0;width:80px;text-align:center}

/* section titles */
.section-title{font-family:"Cinzel",Georgia,serif;font-weight:700;text-align:center;font-size:16px;color:var(--navy)}
.section-title .accent{color:var(--blue)}
.rule{width:190px;height:1px;background:#bbb;margin:4px auto 0;position:relative}
.rule::after{content:"";position:absolute;left:50%;top:-2px;width:5px;height:5px;margin-left:-2.5px;background:var(--blue);transform:rotate(45deg)}

.about{position:absolute;top:528px;left:0;width:721px;padding:0 60px}
.about p{margin-top:10px;font-size:7.5px;line-height:1.55;text-align:center;color:var(--muted)}

.products{position:absolute;top:652px;left:0;width:721px;height:226px;background:var(--grey-band);padding-top:14px}
.product-row{display:flex;justify-content:center;gap:36px;margin-top:14px}
.product{width:120px;text-align:center}
.product svg{display:block;margin:0 auto}
.product-name{font-family:"Cinzel",Georgia,serif;font-weight:700;color:var(--blue);font-size:11px;margin-top:6px}
.product p{font-size:6.5px;line-height:1.45;color:var(--muted);margin:3px 0 6px}

.testimonials{position:absolute;top:888px;left:0;width:721px;height:222px;padding-top:6px}
.testimonial-row{position:relative;display:flex;justify-content:center;align-items:center;gap:90px;margin-top:14px}
.client-photo-side{opacity:.9}
.arrow{position:absolute;top:40px}
.testimonial-name{text-align:center;color:var(--red);font-family:"Cinzel",Georgia,serif;font-weight:700;font-size:10px;margin-top:4px}
.testimonial-quote{text-align:center;font-size:7px;color:var(--muted);line-height:1.45;width:260px;margin:3px auto 0}

.site-footer{position:absolute;top:1114px;left:0;width:721px;height:86px;background:var(--blue-dark);color:#dfe6f2;text-align:center;padding:8px 40px;font-size:6.8px;line-height:1.5}
.site-footer strong{display:block;color:var(--white);font-size:8px}
.copyright{margin-top:6px;color:#b8c5da}
</style>
</head>
<body>

<header class="site-header">
  <div class="brand">Insurance Agent</div>
  <div class="header-actions">
    <span class="btn">GET A QUOTE!</span>
    <span class="phone">
      <svg width="14" height="14" viewBox="0 0 24 24"><path fill="#1f5fa8" d="M6.6 10.8a15 15 0 0 0 6.6 6.6l2.2-2.2c.3-.3.7-.4 1-.2 1.1.4 2.3.6 3.6.6.6 0 1 .4 1 1V20c0 .6-.4 1-1 1A17 17 0 0 1 3 4c0-.6.4-1 1-1h3.5c.6 0 1 .4 1 1 0 1.3.2 2.5.6 3.6.1.3 0 .7-.2 1z"/></svg>
      123 456 7890
    </span>
  </div>
</header>

<div class="hero" role="img" aria-label="Stormy grey sky with a person holding an umbrella seen from behind"></div>

<section class="quote-panel">
  <div class="agent-card">
    <svg class="agent-photo" viewBox="0 0 64 72" role="img" aria-label="Portrait of the insurance agent">
      <polygon points="32,1 63,18 63,54 32,71 1,54 1,18" fill="#9aa3ad" stroke="#fff" stroke-width="2"/>
    </svg>
    <div class="agent-title">Get An Instant Quote</div>
    <div class="agent-line">
      <svg width="8" height="8" viewBox="0 0 24 24"><path fill="#1f5fa8" d="M6.6 10.8a15 15 0 0 0 6.6 6.6l2.2-2.2c.3-.3.7-.4 1-.2 1.1.4 2.3.6 3.6.6.6 0 1 .4 1 1V20c0 .6-.4 1-1 1A17 17 0 0 1 3 4c0-.6.4-1 1-1h3.5c.6 0 1 .4 1 1 0 1.3.2 2.5.6 3.6.1.3 0 .7-.2 1z"/></svg>
      123 456 7890
    </div>
    <div class="agent-line">
      <svg width="8" height="8" viewBox="0 0 24 24"><path fill="#1f5fa8" d="M2 5h20v14H2z"/><path fill="none" stroke="#fff" stroke-width="2" d="M2 5l10 8 10-8"/></svg>
      info@sampleagency.com
    </div>
    <div class="agent-address">Lorem ipsum dolor sit amet, street<br>Adipis cing elit, sed diam nonummy<br>Sample town, 00000</div>
  </div>
  <form class="quote-form">
    <div class="form-title">Get An Instant Insurance Quote</div>
    <div class="form-grid">
      <div class="field"><label>First Name:</label><div class="input"></div></div>
      <div class="field"><label>Insurance Type:</label><div class="input">Select</div></div>
      <div class="field"><label>Last Name:</label><div class="input"></div></div>
      <div class="field"><label>Coverage Amount:</label><div class="input">Select</div></div>
      <div class="field"><label>Date of Birth:</label><div class="dob"><div class="input">Month</div><div class="input">Day</div><div class="input">Year</div></div></div>
      <div class="field"><label>Phone:</label><div class="input"></div></div>
      <div class="field"><label>Zip Code:</label><div class="input"></div></div>
      <div class="field"><label>Email:</label><div class="input"></div></div>
    </div>
    <span class="btn submit">SUBMIT</span>
  </form>
</section>

<section class="about">
  <h2 class="section-title"><span class="accent">About</span> Insurance Agent</h2>
  <div class="rule"></div>
  <p>Lorem ipsum dolor sit amet, consectetuer adipiscing elit, sed diam nonummy nibh euismod tincidunt ut laoreet dolore magna aliquam erat volutpat. Ut wisi enim ad minim veniam, quis nostrud exerci tation ullamcorper suscipit lobortis nisl ut aliquip ex ea commodo consequat. Duis autem vel eum iriure dolor in hendrerit in vulputate velit esse molestie consequat, vel illum dolore eu feugiat nulla facilisis at vero eros et accumsan et iusto odio dignissim qui blandit praesent luptatum zzril delenit augue duis dolore te feugait nulla facilisi.</p>
</section>

<section class="products">
  <h2 class="section-title"><span class="accent">Our</span> Insurance Products</h2>
  <div class="rule"></div>
  <div class="product-row">
    <div class="product">
      <svg width="62" height="70" viewBox="0 0 62 70"><polygon points="31,1 61,18 61,52 31,69 1,52 1,18" fill="var(--hex)"/>
        <g fill="#fff"><rect x="18" y="32" width="16" height="10"/><rect x="22" y="25" width="8" height="8" fill="none" stroke="#fff" stroke-width="2"/><rect x="36" y="20" width="2" height="24"/><rect x="38" y="40" width="8" height="2"/><circle cx="21" cy="45" r="3"/><circle cx="32" cy="45" r="3"/></g></svg>
      <div class="product-name">Life</div>
      <p>Lorem ipsum dolor sit amet, consectetuer adipiscing elit, sed diam nonummy nibh euismod tincidunt.</p>
      <span class="btn">GET A QUOTE!</span>
    </div>
    <div class="product">
      <svg width="62" height="70" viewBox="0 0 62 70"><polygon points="31,1 61,18 61,52 31,69 1,52 1,18" fill="var(--hex)"/>
        <g fill="#fff"><path d="M19 38l4-9h16l4 9v7H19z"/><rect x="25" y="31" width="12" height="5" fill="var(--hex)"/><circle cx="24" cy="41" r="2" fill="var(--hex)"/><circle cx="38" cy="41" r="2" fill="var(--hex)"/><rect x="20" y="44" width="5" height="4"/><rect x="37" y="44" width="5" height="4"/></g></svg>
      <div class="product-name">Auto</div>
      <p>Lorem ipsum dolor sit amet, consectetuer adipiscing elit, sed diam nonummy nibh euismod tincidunt.</p>
      <span class="btn">GET A QUOTE!</span>
    </div>
    <div class="product">
      <svg width="62" height="70" viewBox="0 0 62 70"><polygon points="31,1 61,18 61,52 31,69 1,52 1,18" fill="var(--hex)"/>
        <g fill="#fff"><path d="M31 20l15 13h-4v14H20V33h-4z"/><rect x="28" y="38" width="6" height="9" fill="var(--hex)"/></g></svg>
      <div class="product-name">Home</div>
      <p>Lorem ipsum dolor sit amet, consectetuer adipiscing elit, sed diam nonummy nibh euismod tincidunt.</p>
      <span class="btn">GET A QUOTE!</span>
    </div>
    <div class="product">
      <svg width="62" height="70" viewBox="0 0 62 70"><polygon points="31,1 61,18 61,52 31,69 1,52 1,18" fill="var(--hex)"/>
        <g fill="#fff"><rect x="18" y="27" width="26" height="19" rx="2"/><rect x="26" y="22" width="10" height="6" fill="none" stroke="#fff" stroke-width="2"/><rect x="18" y="35" width="26" height="1.5" fill="var(--hex)"/><rect x="29" y="33" width="4" height="5"/></g></svg>
      <div class="product-name">Business</div>
      <p>Lorem ipsum dolor sit amet, consectetuer adipiscing elit, sed diam nonummy nibh euismod tincidunt.</p>
      <span class="btn">GET A QUOTE!</span>
    </div>
  </div>
</section>

<section class="testimonials">
  <h2 class="section-title"><span class="accent">Client</span> Testimonials</h2>
  <div class="rule"></div>
  <div class="testimonial-row">
    <svg class="arrow" style="left:56px" width="14" height="26" viewBox="0 0 14 26"><path d="M12 2L2 13l10 11" fill="none" stroke="#999" stroke-width="2"/></svg>
    <svg class="client-photo-side" width="70" height="80" viewBox="0 0 70 80" role="img" aria-label="Portrait of a client"><polygon points="35,1 69,20 69,60 35,79 1,60 1,20" fill="#a9adb3"/></svg>
    <svg width="84" height="96" viewBox="0 0 84 96" role="img" aria-label="Portrait of the featured client"><polygon points="42,2 82,25 82,71 42,94 2,71 2,25" fill="#b7a99c" stroke="var(--red)" stroke-width="3"/></svg>
    <svg class="client-photo-side" width="70" height="80" viewBox="0 0 70 80" role="img" aria-label="Portrait of a client"><polygon points="35,1 69,20 69,60 35,79 1,60 1,20" fill="#a9adb3"/></svg>
    <svg class="arrow" style="right:56px" width="14" height="26" viewBox="0 0 14 26"><path d="M2 2l10 11L2 24" fill="none" stroke="#999" stroke-width="2"/></svg>
  </div>
  <div class="testimonial-name">Lorem Ipsum Dolor Sit</div>
  <p class="testimonial-quote">Lorem ipsum dolor sit amet, consectetuer adipiscing elit, sed diam nonummy nibh euismod tincidunt ut laoreet dolore magna aliquam erat volutpat.</p>
</section>

<footer class="site-footer">
  <strong>Disclaimer :</strong>
  Lorem ipsum dolor sit amet, consectetuer adipiscing elit, sed diam nonummy nibh euismod tincidunt ut laoreet dolore magna aliquam erat volutpat. Ut wisi enim ad minim veniam, quis nostrud exerci tation ullamcorper suscipit lobortis nisl ut aliquip ex ea commodo consequat. Duis autem vel eum iriure dolor in hendrerit.
  <div class="copyright">Copyright © 2024 Insurance Agent &nbsp;|&nbsp; All rights reserved.</div>
</footer>

</body>
</html>
```